Cyber Security Site Design (Products & Consulting)

I need my website redesigned to be engaging, clean, efficient and modern. My company (when its up and running) is going to be concentrated on two things: a few specific products for cyber security as well as cyber security consulting services. The background I bring to the field is having worked with small companies all the way to the largest government organizations and advising them on their security posture and how to improve it. We need the ability to add products and services easily.

For a sample product, you can use either Tarnet (http://www.tarnet-relay.org/) or Verodyne Ashmantle (https://www.verodyne.com/products/relay-hx-and-fortified-edge-portal).

It will replace https://lumerafieldworks.com/

Target Market(s)

Cyber Security professionals in all verticals

Coding

Coded - Design and coding required

Number of Pages Required

4 page

Font styles to use
Sans Serif

Colors
6b449b

Requirements
Must have
• Ability to easily modify
• Have main page
• Have product specific pages
• Have consulting services pages
• Have executive team information
• Clean, modern design
• Usage of the logo and its color scheme
Nice to have
• I like the idea of a left collapsed sidebar (so icons only) that can expand for text.
• I am also open to a very unique landing page, possibly a shape in the middle (hexagons maybe?) with each of the options there.
Should not have
• Nothing that looks like it came out of a hacker movie

```html
<!DOCTYPE html>
<html lang="en">
<head>
<meta charset="utf-8">
<title>Lumera Fieldworks — About</title>
<link href="https://fonts.googleapis.com/css2?family=Exo+2:wght@400;500;600;700&family=Montserrat:wght@400;500&family=Roboto:wght@400;500&display=swap" rel="stylesheet">
<style>
:root{
  --purple:#6b449b;
  --purple-footer:#633797;
  --purple-deep:#4f2c7c;
  --ink:#222;
  --text:#333;
  --grey:#b4b4b4;
  --line:#ddd;
  --white:#fff;
}
*{margin:0;padding:0;box-sizing:border-box}
html,body{width:724px;height:1200px;overflow:hidden;background:var(--white)}
body{position:relative;font-family:'Montserrat',sans-serif;color:var(--text)}
h1,h2,h3{font-weight:400}
.abs{position:absolute}

/* header */
.site-header{left:0;top:0;width:724px;height:42px;background:var(--white)}
.brand{left:85px;top:8px;display:flex;align-items:center;gap:5px;font-family:'Exo 2',sans-serif;font-weight:600;font-size:16px;color:var(--purple);letter-spacing:.3px}
.brand-dot{width:20px;height:20px;border-radius:50%;background:var(--purple)}
.main-nav{left:274px;top:17px;display:flex;gap:21px;font-family:'Roboto',sans-serif;font-size:7.6px;color:var(--ink)}
.main-nav .active{color:var(--purple)}
.btn{display:flex;align-items:center;gap:5px;background:var(--purple);color:var(--white);font-family:'Roboto',sans-serif;font-size:7.5px;border-radius:10px;box-shadow:0 2px 4px rgba(0,0,0,.2)}
.btn-dot{width:11px;height:11px;border-radius:50%;border:1.5px solid var(--white)}
.btn-contact{left:559px;top:12px;width:77px;height:19px;padding-left:6px}

/* hero */
.hero{left:0;top:42px;width:724px;height:226px}
.hero-title{left:0;top:112px;width:724px;text-align:center;font-family:'Exo 2',sans-serif;font-weight:600;font-size:26px;color:var(--white);text-shadow:0 1px 3px rgba(0,0,0,.4)}
.hero-sub{left:0;top:145px;width:724px;text-align:center;font-family:'Exo 2',sans-serif;font-size:11px;color:var(--white);text-shadow:0 1px 2px rgba(0,0,0,.5)}
.btn-start{left:309px;top:178px;width:104px;height:19px;padding-left:6px}

.breadcrumb{left:85px;top:260px;font-family:'Roboto',sans-serif;font-size:7.6px;color:var(--ink)}
.breadcrumb span{color:var(--purple)}

/* about */
.section-title{left:0;top:309px;width:724px;text-align:center;font-family:'Exo 2',sans-serif;font-weight:400;font-size:25px;color:var(--ink)}
.section-title b{font-weight:700}
.title-rule{left:281px;top:348px;width:162px;height:1px;background:var(--line)}
.title-accent{left:350px;top:347px;width:25px;height:2px;background:var(--purple)}

.portrait-frame{left:85px;top:369px;width:217px;height:263px}
.portrait-photo{left:96px;top:379px;width:196px;height:242px;background:linear-gradient(180deg,#f3f3f3 0%,#e7e2de 35%,#8a7068 55%,#4a4a4c 80%,#3b3b3d 100%);border-radius:0 14px 0 0}
.portrait-caption{left:96px;top:577px;width:196px;height:44px;background:rgba(30,30,30,.72);text-align:center;color:var(--white)}
.portrait-name{font-family:'Exo 2',sans-serif;font-size:13px;margin-top:7px}
.portrait-role{font-family:'Montserrat',sans-serif;font-size:8.5px;margin-top:2px}

.about-copy{left:324px;top:369px;width:313px;text-align:justify}
.about-copy .lead{font-size:9.3px;line-height:15.1px;color:var(--ink);margin-bottom:8px}
.about-copy p{font-size:8.1px;line-height:13.6px;margin-bottom:6.5px}
.about-wide{left:86px;top:642px;width:552px;text-align:justify}
.about-wide p{font-size:8.1px;line-height:13.6px;margin-bottom:6.5px}

/* footer */
.footer-bg{left:0;top:841px;width:724px;height:329px}
.footer-brand{left:300px;top:865px;display:flex;align-items:center;gap:6px;font-family:'Exo 2',sans-serif;font-weight:600;font-size:20px;color:var(--white)}
.footer-brand .brand-dot{width:30px;height:30px;background:var(--white)}
.footer-rule{left:0;top:910px;width:724px;height:1px;background:rgba(255,255,255,.12)}
.cta-title{left:83px;top:936px;font-family:'Exo 2',sans-serif;font-weight:400;font-size:21px;color:var(--white)}
.cta-title b{font-weight:700}
.cta-text{left:85px;top:968px;width:220px;font-family:'Roboto',sans-serif;font-size:8.3px;line-height:10.5px;color:var(--white)}
.col-head{font-family:'Roboto',sans-serif;font-weight:500;font-size:9.5px;color:var(--white)}
.col-head::after{content:"";display:block;width:26px;height:1px;background:rgba(255,255,255,.7);margin-top:5px}
.contact-col{left:83px;top:1019px;width:150px;color:var(--white);font-family:'Roboto',sans-serif}
.contact-row{display:flex;gap:7px;margin-top:8px;font-size:6.8px;line-height:10px}
.contact-row svg{flex:none;margin-top:1px}
.contact-row strong{font-weight:500;font-size:7.5px}
.contact-row .phone{font-weight:500;font-size:9.5px}
.links-col{left:241px;top:1018px;color:var(--white);font-family:'Roboto',sans-serif}
.links-col ul{list-style:none;margin-top:8px}
.links-col li{font-size:6.8px;line-height:11.6px}
.links-col li::before{content:"›";margin-right:6px}
.form-card{left:370px;top:938px;width:269px;height:232px;background:var(--white)}
.field{left:392px;width:226px;height:23px;border:1px solid #c9c9c9;font-family:'Montserrat',sans-serif;font-size:7px;color:#666;padding:8px 9px 0}
.field-message{height:35px;padding-top:6px}
.btn-submit{left:392px;top:1132px;width:62px;height:19px;padding-left:6px;font-size:7.5px}
.footer-bar{left:0;top:1170px;width:724px;height:30px;background:var(--purple-deep)}
.copyright{left:85px;top:1181px;font-family:'Roboto',sans-serif;font-size:6.8px;color:var(--white)}
.copyright b{font-weight:500}
.socials{left:471px;top:1176px;display:flex;gap:4px}
.socials span{width:17px;height:17px;border-radius:50%;border:1px solid rgba(255,255,255,.85)}
</style>
</head>
<body>

<header class="site-header abs">
  <div class="brand abs"><span class="brand-dot"></span>Lumera Fieldworks</div>
  <nav class="main-nav abs">
    <span>HOME</span><span class="active">ABOUT</span><span>OUR TEAM</span><span>OUR PRODUCTS</span><span>SERVICES</span>
  </nav>
  <div class="btn btn-contact abs"><span class="btn-dot"></span>CONTACT US</div>
</header>

<svg class="hero abs" viewBox="0 0 724 226" role="img" aria-label="Photograph of a downtown city skyline at sunset">
  <defs>
    <linearGradient id="sky" x1="0" y1="0" x2="0" y2="1">
      <stop offset="0" stop-color="#4f5f78"/>
      <stop offset=".35" stop-color="#9a8a8c"/>
      <stop offset=".55" stop-color="#c79a7a"/>
      <stop offset=".75" stop-color="#6f5c52"/>
      <stop offset="1" stop-color="#4a3e38"/>
    </linearGradient>
  </defs>
  <polygon points="0,0 724,0 724,155 362,226 0,155" fill="url(#sky)"/>
</svg>
<h1 class="hero-title abs">CYBER SECURITY CONSULTING &amp; PRODUCTS</h1>
<p class="hero-sub abs">A full range of Cyber Security Consulting Services and Products to meet your business requirements</p>
<div class="btn btn-start abs"><span class="btn-dot"></span>GET STARTED NOW!</div>

<div class="breadcrumb abs">HOME &nbsp;&nbsp;»&nbsp;&nbsp; <span>ABOUT</span></div>

<h2 class="section-title abs">ABOUT <b>US</b></h2>
<div class="title-rule abs"></div>
<div class="title-accent abs"></div>

<svg class="portrait-frame abs" viewBox="0 0 217 263">
  <rect x="0" y="0" width="37" height="38" fill="var(--purple)"/>
  <path d="M43 0 H197 A20 20 0 0 1 217 20 V220 H207 V10 H43 Z" fill="var(--grey)"/>
  <path d="M0 45 V243 A20 20 0 0 0 20 263 H173 V253 H11 V45 Z" fill="var(--purple)"/>
  <rect x="180" y="227" width="37" height="36" fill="var(--purple)"/>
</svg>
<div class="portrait-photo abs" role="img" aria-label="Portrait photograph of the company founder in a grey blazer"></div>
<div class="portrait-caption abs">
  <div class="portrait-name">Daniel Korvath Mellinger</div>
  <div class="portrait-role">Founder &amp; CEO</div>
</div>

<div class="about-copy abs">
  <p class="lead">We are a company that takes its roots from the idea of providing appropriate and creative solutions for cyber security operations, development and management. We have a mission first mindset for our clients and their objectives.</p>
  <p>We are located in the Raleigh / Durham, NC, USA area but are able to work with clients world-wide. Please contact us for any inquires you may have and we will be glad to assist you in any way possible.</p>
  <p>Lorem ipsum dolor sit amet, consectetur adipiscing elit, sed do eiusmod tempor incididunt ut labore et dolore magna aliqua. Ut enim ad minim veniam, quis nostrud exercitation ullamco laboris nisi ut aliquip ex ea commodo consequat.Duis aute irure dolor in reprehenderit in voluptate velit esse cillum dolore eu fugiat nulla pariatur. Excepteur sint occaecat cupidatat non proident, sunt in culpa qui officia deserunt mollit anim id est laborum.</p>
  <p>Lorem ipsum dolor sit amet, consectetur adipiscing elit, sed do eiusmod tempor incididunt ut labore et dolore magna aliqua. Ut enim ad minim veniam, quis nostrud exercitation ullamco laboris nisi.</p>
</div>

<div class="about-wide abs">
  <p>Sed ut perspiciatis unde omnis iste natus error sit voluptatem accusantium doloremque laudantium, totam rem aperiam, eaque ipsa quae ab illo inventore veritatis et quasi architecto beatae vitae dicta sunt explicabo. Nemo enim ipsam voluptatem quia voluptas sit aspernatur aut odit aut fugit, sed quia consequuntur magni dolores eos qui ratione voluptatem sequi nesciunt. Neque porro quisquam est, qui dolorem ipsum quia dolor sit amet, consectetur, adipisci velit, sed quia non numquam eius modi tempora incidunt ut labore et dolore magnam aliquam quaerat voluptatem. Ut enim ad minima veniam, quis nostrum exercitationem ullam corporis suscipit laboriosam, nisi ut aliquid ex ea commodi consequatur? Quis autem vel eum iure reprehenderit qui in ea voluptate velit esse quam nihil molestiae consequatur, vel illum qui dolorem eum fugiat quo voluptas nulla pariatur</p>
  <p>Lorem ipsum dolor sit amet, consectetur adipiscing elit, sed do eiusmod tempor incididunt ut labore et dolore magna aliqua. Ut enim ad minim veniam, quis nostrud exercitation ullamco laboris nisi ut aliquip ex ea commodo consequat. Duis aute irure dolor in reprehenderit in voluptate velit esse cillum dolore eu fugiat nulla pariatur. Excepteur sint occaecat cupidatat non proident, sunt in culpa qui officia deserunt mollit anim id est laborum.</p>
</div>

<footer>
  <svg class="footer-bg abs" viewBox="0 0 724 329">
    <polygon points="0,27 362,2 724,27 724,329 0,329" fill="var(--purple-footer)"/>
  </svg>
  <div class="footer-brand abs"><span class="brand-dot"></span>Lumera Fieldworks</div>
  <div class="footer-rule abs"></div>

  <h3 class="cta-title abs"><b>LET’S</b> GET STARTED</h3>
  <p class="cta-text abs">Take the first step to growing your business with a FREE consultation and quote.</p>

  <div class="contact-col abs">
    <div class="col-head">Contact Details</div>
    <div class="contact-row">
      <svg width="7" height="9" viewBox="0 0 7 9"><path d="M3.5 0A3.3 3.3 0 0 0 .2 3.3C.2 5.6 3.5 9 3.5 9S6.8 5.6 6.8 3.3A3.3 3.3 0 0 0 3.5 0Z" fill="var(--white)"/><circle cx="3.5" cy="3.3" r="1.2" fill="var(--purple-footer)"/></svg>
      <div><strong>LUMERA CYBER SECURITY</strong><br>4810 Alder Ridge Rd, Suite<br>#212 Cary, NC 27513.</div>
    </div>
    <div class="contact-row">
      <svg width="8" height="8" viewBox="0 0 8 8"><path d="M1.6 0.3 2.9 2 2.2 3.1C2.8 4.4 3.6 5.2 4.9 5.8L6 5.1 7.7 6.4 7 7.7C3.5 7.6.4 4.5.3 1Z" fill="var(--white)"/></svg>
      <span class="phone">123-555-0148</span>
    </div>
    <div class="contact-row">
      <svg width="8" height="7" viewBox="0 0 8 7"><rect x="0" y="1" width="8" height="6" fill="var(--white)"/><path d="M0 1.3 4 4.3 8 1.3" fill="none" stroke="var(--purple-footer)" stroke-width=".8"/></svg>
      <span>info@lumeracybersecurity.com</span>
    </div>
  </div>

  <div class="links-col abs">
    <div class="col-head">Quick Links</div>
    <ul>
      <li>Home</li><li>About Us</li><li>Our Team</li><li>Our Products</li><li>Services</li><li>Conatact</li>
    </ul>
  </div>

  <div class="form-card abs"></div>
  <div class="field abs" style="top:962px">First Name</div>
  <div class="field abs" style="top:992px">Last Name</div>
  <div class="field abs" style="top:1022px">Email</div>
  <div class="field abs" style="top:1052px">Phone Number</div>
  <div class="field field-message abs" style="top:1081px">Message</div>
  <div class="btn btn-submit abs"><span class="btn-dot"></span>SUBMIT</div>

  <div class="footer-bar abs"></div>
  <p class="copyright abs">Copyright © 2018 <b>LumeraCyberSecurity</b>. All Right Reserved.</p>
  <div class="socials abs" aria-label="Social links"><span></span><span></span><span></span><span></span></div>
</footer>

</body>
</html>
```